International service dog training school needs web design

We need to upgrade our website. The website is https://brightmeadow.studio/
We help trainers and service dog programs learn how to train service dogs with the latest and most ethical training methods. We offer online and in-person coaching services. We would like to see designs that are engaging and communicate professionalism, expertise, and care for the dogs and people we work with. Please also keep the colors already in the logo in the design.

```html
<!DOCTYPE html>
<html lang="en">
<head>
<meta charset="utf-8">
<title>Marion Delacroix Ph.D. — Meadowbrook Institute of Alert &amp; Assistance Dogs</title>
<link href="https://fonts.googleapis.com/css2?family=Saira+Condensed:wght@500;600&family=Lato:wght@400;700&display=swap" rel="stylesheet">
<style>
:root{
  --teal:#12a89d;
  --blue:#1e72b8;
  --ink:#333;
  --muted:#444;
  --soft:#f5f5f5;
  --white:#fff;
  --black:#000;
  --head:"Saira Condensed",sans-serif;
  --body:"Lato",sans-serif;
}
*{box-sizing:border-box;margin:0;padding:0}
html,body{width:1200px;height:3070px;overflow:hidden}
body{position:relative;background:var(--white);font-family:var(--body);color:var(--ink)}
.abs{position:absolute}
/* hero */
.hero{left:0;top:0;width:1200px;height:670px;
  background:radial-gradient(ellipse at 78% 45%,#c98a5a 0,#d7a57a 18%,rgba(230,200,165,.9) 38%,rgba(220,215,200,.6) 60%),
  linear-gradient(180deg,#eef0ec 0,#e2d3bd 45%,#cfae86 80%,#b88c62 100%)}
.hero-ring{left:660px;top:120px;width:300px;height:330px;border-radius:50%;border:12px solid rgba(18,168,157,.28);border-left-color:transparent;border-bottom-color:rgba(18,168,157,.18)}
.hero-curve{left:0;top:560px}
.header{left:0;top:0;width:1200px;height:110px}
.brand{left:48px;top:22px;display:flex;align-items:center;gap:10px}
.brand-dot{width:50px;height:50px;border-radius:50%;border:3px solid var(--blue)}
.brand-name{font-family:var(--head);font-weight:500;color:var(--blue);font-size:21px;line-height:1.05}
.brand-name small{display:block;font-size:15px;line-height:1.1;text-transform:uppercase}
.nav{left:367px;top:40px;display:flex;gap:30px;font-family:var(--head);font-weight:500;font-size:14.5px;color:#222;text-transform:uppercase;white-space:nowrap}
.call{left:978px;top:24px;display:flex;align-items:center;gap:10px}
.call-icon{width:50px;height:50px;border-radius:50%;background:var(--blue);display:flex;align-items:center;justify-content:center;box-shadow:0 0 0 4px rgba(255,255,255,.8),0 0 0 6px var(--teal)}
.call-label{font-size:12px;color:var(--blue)}
.call-num{font-family:var(--head);font-weight:600;font-size:25px;color:var(--teal);line-height:1}
.hero-title{left:82px;top:176px;font-family:var(--head);font-weight:500;font-size:60px;line-height:77px;text-transform:uppercase;color:var(--blue);white-space:nowrap}
.hero-title .alt{color:var(--teal)}
.btn{display:flex;align-items:center;justify-content:center;border-radius:30px;font-family:var(--head);font-weight:500;text-transform:uppercase;font-size:16px}
.btn-solid{background:var(--teal);color:var(--white)}
.btn-line{border:2px solid var(--teal);color:var(--teal);background:var(--white)}
.hero-btn{left:82px;top:432px;width:172px;height:52px}
.dots{left:572px;top:594px;display:flex;gap:4px}
.dots span{width:9px;height:9px;border-radius:50%;background:var(--white)}
.dots span:first-child{background:var(--teal)}
/* about */
.about{left:0;top:670px;width:1200px;height:424px;background:var(--soft)}
.section-title{font-family:var(--head);font-weight:500;font-size:30px;color:var(--teal);text-transform:uppercase}
.rule{width:26px;height:4px;background:var(--blue)}
.about-title{left:0;top:736px;width:1200px;text-align:center}
.about-rule{left:588px;top:784px}
.about-text{left:172px;top:808px;width:856px;text-align:center;font-size:14px;line-height:28px;color:var(--muted)}
.about-btn{left:514px;top:963px;width:172px;height:51px}
/* services */
.svc-photo{width:420px;height:420px}
.svc-title{font-family:var(--head);font-weight:500;font-size:26px;line-height:34px;color:var(--blue);text-transform:uppercase;width:420px}
.svc-rule{margin:14px 0 16px 2px}
.svc-text{font-size:14.5px;line-height:28px;color:var(--muted);width:450px;padding-left:3px}
.svc-text.narrow{width:430px}
.svc-btn{width:176px;height:55px;margin-top:20px;font-size:18px}
.pager{left:522px;top:2493px;display:flex;align-items:center;gap:16px;font-size:14px;color:#333}
.pager .on{color:var(--teal)}
/* footer */
.footer-curve{left:0;top:2596px}
.footer{left:0;top:2690px;width:1200px;height:380px;background:var(--black)}
.foot-brand{left:0;top:2710px;width:1200px;display:flex;justify-content:center;align-items:center;gap:16px}
.foot-dot{width:110px;height:110px;border-radius:50%;border:5px solid var(--white)}
.foot-name{font-family:var(--head);font-weight:500;color:var(--white);font-size:42px;line-height:1}
.foot-name small{display:block;font-size:32px;line-height:1.1;margin-top:4px;text-transform:uppercase}
.foot-nav{left:367px;top:2848px;display:flex;gap:30px;font-family:var(--head);font-weight:500;font-size:14.5px;color:var(--white);text-transform:uppercase;white-space:nowrap}
.social{left:461px;top:2900px;display:flex;gap:12px}
.social span{width:60px;height:60px;border-radius:50%;background:var(--teal);box-shadow:0 0 0 4px #0b5e58}
.copy{left:0;top:2986px;width:1200px;text-align:center;font-size:14px;color:var(--white)}
</style>
</head>
<body>

<div class="abs hero" role="img" aria-label="Photo of a short-haired reddish-brown hunting dog sitting in a sunlit meadow of dry grass"></div>
<div class="abs hero-ring"></div>
<svg class="abs hero-curve" width="1200" height="110" viewBox="0 0 1200 110">
  <path d="M0 20 Q600 150 1200 20 L1200 110 L0 110 Z" fill="#f5f5f5"/>
  <path d="M18 28 Q600 140 1182 28" fill="none" stroke="#1e72b8" stroke-width="5"/>
  <path d="M18 36 Q600 150 1182 34" fill="none" stroke="#12a89d" stroke-width="5"/>
</svg>

<header class="abs header">
  <div class="abs brand">
    <span class="brand-dot"></span>
    <div class="brand-name">Marion Delacroix Ph.D.<small>Meadowbrook Institute of<br>Alert &amp; Assistance Dogs</small></div>
  </div>
  <nav class="abs nav"><span>Home</span><span>The Center</span><span>Helping Organizations</span><span>Teaching Trainers</span><span>Research Contact</span></nav>
  <div class="abs call">
    <span class="call-icon"><svg width="18" height="18" viewBox="0 0 24 24"><path d="M6.6 10.8a15 15 0 006.6 6.6l2.2-2.2a1 1 0 011-.25 11 11 0 003.6.6 1 1 0 011 1V20a1 1 0 01-1 1A17 17 0 013 4a1 1 0 011-1h3.5a1 1 0 011 1 11 11 0 00.6 3.6 1 1 0 01-.25 1z" fill="#fff"/></svg></span>
    <div><div class="call-label">Call Us Today</div><div class="call-num">123 456 7890</div></div>
  </div>
</header>

<h1 class="abs hero-title">The Meadowbrook<br><span class="alt">Institute of Alert</span><br>&amp; Assistance Dogs</h1>
<a class="abs btn btn-solid hero-btn">Get Started</a>
<div class="abs dots"><span></span><span></span><span></span><span></span><span></span></div>

<section class="abs about"></section>
<h2 class="abs section-title about-title">Who We Are</h2>
<div class="abs rule about-rule"></div>
<p class="abs about-text">The Meadowbrook Institute of Alert &amp; Assistance Dogs was founded by Marion Delacroix Ph.D. in response to demand for coaching from dog trainers, medical professionals, and service dog programs. Marion Delacroix Ph.D. has helped hundreds of trainers and several programs both in the US and internationally, expand the type of dogs they could offer to include medical alert dogs. Specialized mostly in the training of diabetic alert dogs, seizure dogs, and psychiatric service dogs, Marion Delacroix is also experienced in the training of mobility assistance dogs and autism dogs. The coaching is individually catered to meet the programs’ needs.</p>
<a class="abs btn btn-solid about-btn">Learn More</a>

<svg class="abs svc-photo" style="left:130px;top:1162px" viewBox="0 0 420 420" role="img" aria-label="Group photo of trainers in matching light blue shirts with several dogs">
  <defs><linearGradient id="g1" x1="0" y1="0" x2="0" y2="1"><stop offset="0" stop-color="#d9dde2"/><stop offset=".55" stop-color="#8fa9c8"/><stop offset="1" stop-color="#b7a58c"/></linearGradient></defs>
  <circle cx="210" cy="210" r="188" fill="url(#g1)"/>
  <circle cx="210" cy="210" r="200" fill="none" stroke="#12a89d" stroke-width="13" stroke-dasharray="420 208" transform="rotate(-150 210 210)"/>
</svg>
<div class="abs" style="left:595px;top:1290px">
  <h3 class="svc-title">Organization/Program Consulting</h3>
  <div class="rule svc-rule"></div>
  <p class="svc-text">Helping organizations get started, improve their training program, and add services</p>
  <a class="btn btn-line svc-btn">Learn More</a>
</div>

<svg class="abs svc-photo" style="left:650px;top:1600px" viewBox="0 0 420 420" role="img" aria-label="Trainer in a brown jacket working with a black dog indoors">
  <defs><linearGradient id="g2" x1="0" y1="0" x2="0" y2="1"><stop offset="0" stop-color="#e4e1d8"/><stop offset=".5" stop-color="#6e5244"/><stop offset="1" stop-color="#7a8aa8"/></linearGradient></defs>
  <circle cx="210" cy="210" r="188" fill="url(#g2)"/>
  <circle cx="210" cy="210" r="200" fill="none" stroke="#12a89d" stroke-width="13" stroke-dasharray="420 208" transform="rotate(-150 210 210)"/>
</svg>
<div class="abs" style="left:134px;top:1708px">
  <h3 class="svc-title" style="width:400px">Professional Coaching/Teaching for Dog Trainers</h3>
  <div class="rule svc-rule"></div>
  <p class="svc-text">Helping dog trainers improve their skills and learn about service dog training and medical alert dog training.</p>
  <a class="btn btn-line svc-btn">Learn More</a>
</div>

<svg class="abs svc-photo" style="left:130px;top:2040px" viewBox="0 0 420 420" role="img" aria-label="Light-coated dog in a green vest sniffing a metal scent tin on a tiled floor">
  <defs><linearGradient id="g3" x1="0" y1="0" x2="0" y2="1"><stop offset="0" stop-color="#e8e2d6"/><stop offset=".5" stop-color="#d6d2ca"/><stop offset="1" stop-color="#c9c6c2"/></linearGradient></defs>
  <circle cx="210" cy="210" r="188" fill="url(#g3)"/>
  <circle cx="210" cy="210" r="200" fill="none" stroke="#12a89d" stroke-width="13" stroke-dasharray="420 208" transform="rotate(-150 210 210)"/>
</svg>
<div class="abs" style="left:595px;top:2166px">
  <h3 class="svc-title">Collaborating in Research Projects</h3>
  <div class="rule svc-rule"></div>
  <p class="svc-text narrow">Collaborating in research studies in the field of Medical Detection Dogs.</p>
  <a class="btn btn-line svc-btn">Learn More</a>
</div>

<div class="abs pager">
  <svg width="10" height="14" viewBox="0 0 10 14"><path d="M8 1L2 7l6 6" fill="none" stroke="#12a89d" stroke-width="3"/></svg>
  <span><span class="on">01</span> 02 .......07</span>
  <svg width="10" height="14" viewBox="0 0 10 14"><path d="M2 1l6 6-6 6" fill="none" stroke="#12a89d" stroke-width="3"/></svg>
</div>

<svg class="abs footer-curve" width="1200" height="100" viewBox="0 0 1200 100">
  <path d="M0 94 Q600 -20 1200 94 L1200 100 L0 100 Z" fill="#000"/>
  <path d="M18 82 Q600 -26 1182 82" fill="none" stroke="#1e72b8" stroke-width="5"/>
  <path d="M18 90 Q600 -18 1182 90" fill="none" stroke="#12a89d" stroke-width="5"/>
</svg>
<footer class="abs footer"></footer>
<div class="abs foot-brand">
  <span class="foot-dot"></span>
  <div class="foot-name">Marion Delacroix Ph.D.<small>Meadowbrook Institute of<br>Alert &amp; Assistance Dogs</small></div>
</div>
<nav class="abs foot-nav"><span>Home</span><span>The Center</span><span>Helping Organizations</span><span>Teaching Trainers</span><span>Research Contact</span></nav>
<div class="abs social"><span aria-label="Social link"></span><span aria-label="Social link"></span><span aria-label="Social link"></span><span aria-label="Social link"></span></div>
<p class="abs copy">© Copyright 2021 Company Name &nbsp; | &nbsp; All Rights Reserved</p>

</body>
</html>
```